Report-Design  für Social-Media-Beratungs-Agentur
Report-Design für Social-Media-Beratungs-Agentur
Zielgruppe
Wir sind eine Social-Media-Beratungs-Agentur, die KMU bei der strategischen Ausrichtung und Umsetzung ihrer Social-Media-Präsenzen berät und unterstützt.
Aufgabenstellung
Wir analysieren die Vernetra Profile von Unternehmen in einer Excel-Datei, indem wir in einem Reiter verschiedene Aspekte bewerten. Aus diesen Bewertungen ergibt sich dann in einem zweiten Reiter ein Report (hängt hier an), in den die Ergebnisse aus der 1. Mappe automatisch übernommen werden. Dieser Report wird als PDF gespeichert und an den Kunden geschickt. Wir möchten das Report-Design gerne neu gestalten lassen: Es soll zeitgemäß, professionell und kompetent wirken und nicht mehr 'wie in Excel zusammengebastelt'. Ein Beispiel für ein Design, das uns gefällt, hängt als Inspiration an. Gerne können Grafikelemente aus Canva oder anderen Grafikprogrammen eingefügt werden. Wichtig ist, dass die Struktur mit den Zellen, in die Daten automatisch übernommen werden (im Anhang durch # gekennzeichnet), erhalten bleibt. Unsere Firmenfarben sind: #f69f25, #11323a, #809398, #fcfefd. Wir haben noch weitere Analysen, die wir bei Erfolg dieses Auftrags ebenfalls gerne optimieren lassen möchten.

```html
<!DOCTYPE html>
<html lang="de">
<head>
<meta charset="utf-8">
<title>Social Media Performance Report</title>
<link rel="stylesheet" href="https://fonts.googleapis.com/css2?family=Inter:wght@400;500;600;700&display=swap">
<style>
  :root {
    --page-bg: #e3e9e8;
    --card-bg: #fcfefd;
    --ink: #111416;
    --ink-soft: #3c4245;
    --rule: #d4d8d9;
    --frame: #b9bfc1;
    --accent-slate: #5f7f98;
    --accent-green: #6ea58d;
    --accent-coral: #f27d6c;
    --accent-yellow: #f8c84a;
    --accent-sky: #9dc4d6;
    --brand-navy: #11323a;
  }
  * { box-sizing: border-box; margin: 0; padding: 0; }
  html, body {
    width: 1200px; height: 900px; overflow: hidden;
    background: var(--page-bg);
    font-family: "Inter", sans-serif;
    color: var(--ink);
  }
  .report {
    position: absolute; left: 40px; top: 46px;
    width: 1120px; height: 808px;
    background: var(--card-bg);
    border-radius: 22px;
  }
  .brand {
    position: absolute; left: 41px; top: 38px;
    display: flex; align-items: center; gap: 8px;
    font-size: 17px; font-weight: 600; color: var(--brand-navy);
  }
  .brand-mark { width: 14px; height: 14px; background: var(--brand-navy); border-radius: 3px; }
  .header-rule {
    position: absolute; left: 140px; right: 44px; top: 55px;
    height: 1px; background: var(--rule);
  }
  .report-title {
    position: absolute; left: 44px; top: 142px;
    font-size: 50px; line-height: 1.02; font-weight: 600; letter-spacing: -0.5px;
  }
  .tile { position: absolute; border-radius: 9px; }
  .panel {
    border: 1.5px solid var(--frame);
    background: var(--card-bg);
    padding: 22px 36px;
  }
  .panel::before {
    content: ""; position: absolute; left: -1.5px; top: -1.5px;
    width: 52px; height: 28px;
    border-top: 11px solid var(--accent);
    border-left: 11px solid var(--accent);
    border-top-left-radius: 9px;
  }
  .accent-slate { --accent: var(--accent-slate); }
  .accent-green { --accent: var(--accent-green); }
  .accent-coral { --accent: var(--accent-coral); }
  .accent-yellow { --accent: var(--accent-yellow); }

  .panel-title { font-size: 15px; font-weight: 600; line-height: 1.3; }
  .panel-sub { font-size: 14px; color: var(--ink-soft); line-height: 1.35; }
  .metric-list { list-style: none; margin-top: 14px; }
  .metric-list li {
    display: flex; align-items: center; gap: 12px;
    font-size: 14px; color: var(--ink-soft); height: 29px;
  }
  .metric-list svg { width: 15px; height: 15px; flex: none; }

  .chart-panel .bars { position: absolute; left: 50px; top: 58px; }

  .photo { overflow: hidden; }
  .photo-team-lounge { background: linear-gradient(135deg, #d8dcdc 0%, #a9adad 45%, #6c7070 100%); }
  .photo-portrait { background: linear-gradient(160deg, #eceeee 0%, #c9c6c1 50%, #3a3633 100%); }
  .photo-standing-team { background: linear-gradient(180deg, #e4e4e2 0%, #cfcdca 55%, #5b5855 100%); }
  .photo-meeting { background: linear-gradient(150deg, #cfd2d3 0%, #e6e3de 45%, #8c8780 100%); }
</style>
</head>
<body>
<main class="report">
  <div class="brand"><span class="brand-mark"></span>Vernetra</div>
  <div class="header-rule"></div>

  <h1 class="report-title">Social Media<br>Performance<br>Report</h1>

  <section class="tile panel chart-panel accent-slate" style="left:399px; top:110px; width:322px; height:210px;">
    <p class="panel-title" style="padding-left:0">Vernetra Media</p>
    <p class="panel-sub">Sektion Bericht</p>
    <svg class="bars" width="230" height="130" viewBox="0 0 230 130" aria-label="Balkendiagramm">
      <rect x="2" y="63" width="24" height="55" rx="3" fill="var(--accent-slate)"/>
      <rect x="38" y="85" width="24" height="33" rx="3" fill="var(--accent-green)"/>
      <rect x="76" y="66" width="24" height="52" rx="3" fill="var(--accent-coral)"/>
      <rect x="113" y="82" width="24" height="36" rx="3" fill="var(--accent-yellow)"/>
      <rect x="151" y="44" width="24" height="74" rx="3" fill="var(--accent-green)"/>
      <rect x="190" y="4" width="24" height="114" rx="3" fill="var(--accent-sky)"/>
    </svg>
  </section>

  <div class="tile photo photo-team-lounge" role="img" aria-label="Foto: Team sitzt im Kreis in einem hellen Besprechungsraum" style="left:751px; top:110px; width:325px; height:210px;"></div>

  <section class="tile panel accent-green" style="left:43px; top:348px; width:325px; height:174px;">
    <p class="panel-title">Reichweite</p>
    <p class="panel-sub">Engagement Auswertung,</p>
    <ul class="metric-list">
      <li><svg viewBox="0 0 16 16"><circle cx="8" cy="8" r="6.5" fill="none" stroke="currentColor" stroke-width="1.4"/><path d="M8 4.5V8l-2 2" fill="none" stroke="currentColor" stroke-width="1.4"/></svg>10 Beiträge bewertet gesamt</li>
      <li><svg viewBox="0 0 16 16"><circle cx="8" cy="8" r="6.5" fill="none" stroke="currentColor" stroke-width="1.4"/><path d="M8 4.5V8l-2 2" fill="none" stroke="currentColor" stroke-width="1.4"/></svg>#F69F25</li>
      <li><svg viewBox="0 0 16 16"><circle cx="8" cy="8" r="6.5" fill="none" stroke="currentColor" stroke-width="1.4"/><path d="M8 4.5V8l-2 2" fill="none" stroke="currentColor" stroke-width="1.4"/></svg>#FCFEFD</li>
    </ul>
  </section>

  <div class="tile photo photo-portrait" role="img" aria-label="Foto: lächelnde Person vor Unterlagen mit Diagrammen" style="left:399px; top:348px; width:322px; height:174px;"></div>

  <section class="tile panel accent-coral" style="left:751px; top:348px; width:325px; height:174px;">
    <p class="panel-title">Performance</p>
    <p class="panel-sub">Engagement Auswertung,</p>
    <ul class="metric-list">
      <li><svg viewBox="0 0 16 16"><circle cx="8" cy="8" r="6.5" fill="none" stroke="currentColor" stroke-width="1.4"/><path d="M8 4.5V8l-2 2" fill="none" stroke="currentColor" stroke-width="1.4"/></svg>10 Posts bewertet gesamt</li>
      <li><svg viewBox="0 0 16 16"><circle cx="8" cy="8" r="6.5" fill="none" stroke="currentColor" stroke-width="1.4"/><path d="M8 4.5V8l-2 2" fill="none" stroke="currentColor" stroke-width="1.4"/></svg>#809398</li>
      <li><svg viewBox="0 0 16 16"><circle cx="8" cy="8" r="6.5" fill="none" stroke="currentColor" stroke-width="1.4"/><path d="M8 4.5V8l-2 2" fill="none" stroke="currentColor" stroke-width="1.4"/></svg>#FCFEFD</li>
    </ul>
  </section>

  <div class="tile photo photo-standing-team" role="img" aria-label="Foto: vier Kolleginnen und Kollegen im Gespräch vor heller Wand" style="left:43px; top:552px; width:325px; height:203px;"></div>

  <section class="tile panel accent-yellow" style="left:399px; top:552px; width:322px; height:203px;">
    <p class="panel-title">Aktuelle Analyse</p>
    <p class="panel-sub">Bereiche</p>
    <p class="panel-title" style="margin-top:14px">Abschließende Empfehlungen</p>
    <p class="panel-sub">Strategien</p>
    <ul class="metric-list" style="margin-top:10px">
      <li><svg viewBox="0 0 16 16"><circle cx="8" cy="8" r="6.5" fill="none" stroke="currentColor" stroke-width="1.4"/><path d="M8 4.5V8l-2 2" fill="none" stroke="currentColor" stroke-width="1.4"/></svg>#11323A</li>
      <li><svg viewBox="0 0 16 16"><circle cx="8" cy="8" r="6.5" fill="none" stroke="currentColor" stroke-width="1.4"/><path d="M8 4.5V8l-2 2" fill="none" stroke="currentColor" stroke-width="1.4"/></svg>#FCFEFD</li>
    </ul>
  </section>

  <div class="tile photo photo-meeting" role="img" aria-label="Foto: Team am Tisch mit Laptop vor einem Bildschirm mit Diagrammen" style="left:751px; top:552px; width:325px; height:203px;"></div>
</main>
</body>
</html>
```